Infoblatt
Zielgruppe
Talentförderung, Personalentwicklung, Beratung von Personalabteilungen
Zielgruppe: Personaler, HR Verantwortliche
Aufgabenstellung
Es geht um einen "One-Pager", der auf einem Kongress ausgelegt werden soll und in Kurzform einen Überblick über unser Unternehmen und unser Angebot informieren soll.
Wir haben Visitenkarten auf Recyclingpapier und möchten das Blatt konsistent auf das gleiche Papier drucken lassen, daher einfarbig schwarz. Format DIN A4 Hoch.
IDEE: Vom Stil wie eine Infografik aufbauen
TYPO: unser LOGO ist BEBAS NEUE und unsere Schrift Helvetica

```html
<!DOCTYPE html>
<html lang="de">
<head>
<meta charset="utf-8">
<title>WERKSINN – Infoblatt</title>
<link href="https://fonts.googleapis.com/css2?family=Archivo+Black&family=Arimo:wght@400;700&display=swap" rel="stylesheet">
<style>
  :root{
    --frame:#cdbba0;
    --paper:#ffffff;
    --ink:#000000;
    --tint:#d9d9db;
    --photo-light:#e6e6e6;
    --photo-mid:#bdbdbd;
    --portrait:#cfcfcf;
  }
  *{margin:0;padding:0;box-sizing:border-box}
  html,body{width:1200px;height:848px;overflow:hidden;background:var(--frame)}
  body{position:relative;font-family:"Arimo",Helvetica,Arial,sans-serif;color:var(--ink)}
  .page{position:absolute;top:25px;width:568px;height:803px;background:var(--paper);overflow:hidden}
  .page--cover{left:24px}
  .page--info{left:608px}
  .page svg{position:absolute;left:0;top:0}

  .cover-name{position:absolute;left:136px;top:494px;font-family:"Arimo",Helvetica,Arial,sans-serif;font-weight:700;font-size:68px;line-height:1;color:var(--paper);letter-spacing:1px}
  .cover-contact{position:absolute;left:139px;top:558px;display:flex;gap:14px;font-size:9.4px;color:var(--paper)}

  .hub-name{position:absolute;left:188px;top:365px;width:190px;text-align:center;font-weight:700;font-size:30px;line-height:1;color:var(--paper)}

  .block{position:absolute;width:170px}
  .block h2{font-family:"Archivo Black","Arial Black",sans-serif;font-size:17px;line-height:1;letter-spacing:.5px;font-weight:400}
  .block h3{font-size:12.5px;font-weight:700;margin-top:3px;line-height:1.1}
  .block p{font-size:7.8px;line-height:10.3px;margin-top:10px;text-align:justify}
  .block p + p{margin-top:10px}
  .block strong{font-weight:700}
  .block--credo{left:34px;top:181px}
  .block--value{left:34px;top:469px}
  .block--mission{left:371px;top:469px;width:160px}
  .block--mission h2,.block--mission h3{text-align:right}
  .block--mission p{text-align:left}
  .block--mission ul{list-style:none;font-size:7.8px;line-height:10.3px}
  .block--mission li::before{content:"\25BA";font-size:6.5px;margin-right:1px}
</style>
</head>
<body>

<section class="page page--cover">
  <svg width="568" height="803" viewBox="0 0 568 803">
    <defs>
      <linearGradient id="photoTop" x1="0" y1="0" x2="0" y2="1">
        <stop offset="0" stop-color="#d8d8d8"/><stop offset="1" stop-color="#eeeeee"/>
      </linearGradient>
      <linearGradient id="photoBottom" x1="0" y1="0" x2="1" y2="1">
        <stop offset="0" stop-color="#e2e2e2"/><stop offset="1" stop-color="#b8b8b8"/>
      </linearGradient>
    </defs>
    <rect class="photo" x="0" y="0" width="568" height="458" fill="url(#photoTop)" role="img" aria-label="Foto: Flipchart-Papier mit Markern vor einer Holzwand, schwarz-weiß"/>
    <rect class="photo" x="0" y="473" width="568" height="330" fill="url(#photoBottom)" role="img" aria-label="Foto: Pinnnadeln und Papierrollen auf einem Tisch, schwarz-weiß"/>
    <path class="swoosh" d="M132 458 C 300 400, 470 300, 568 140 L568 458 Z" fill="#000"/>
    <path class="title-field" d="M125 473 H568 V539 C470 600, 330 680, 249 803 H125 Z" fill="#000"/>
  </svg>
  <div class="cover-name">WERKSINN</div>
  <div class="cover-contact">
    <span>Almweg 12 - 14</span><span>42000 Talstadt</span><span>Fon. 0123.45678901</span><span>info@werksinn.de</span>
  </div>
</section>

<section class="page page--info">
  <svg width="568" height="803" viewBox="0 0 568 803">
    <defs>
      <filter id="shadow" x="-30%" y="-30%" width="170%" height="170%">
        <feDropShadow dx="5" dy="5" stdDeviation="2.5" flood-color="#000" flood-opacity=".75"/>
      </filter>
    </defs>
    <polygon class="tint" points="0,152 436,461 436,803 136,803 0,545" fill="var(--tint)"/>
    <polygon class="tint" points="0,150 14,170 0,172" fill="var(--tint)"/>

    <g class="connectors" fill="none" stroke="#000" stroke-width="4">
      <polyline points="151,176 284,176 284,300"/>
      <polyline points="37,449 37,377 195,377"/>
      <polyline points="372,380 524,380 524,449"/>
    </g>

    <g class="hub">
      <circle cx="283" cy="389" r="95" fill="#000"/>
      <path d="M283 470 L283 488 C 305 488, 320 484, 330 478 C 350 460, 360 440, 370 420 Z" fill="#000"/>
      <circle cx="283" cy="389" r="95" fill="#000"/>
    </g>

    <g class="team" filter="url(#shadow)">
      <circle cx="251" cy="86" r="50" fill="var(--portrait)" role="img" aria-label="Porträt Teammitglied"/>
      <circle cx="367" cy="92" r="50" fill="var(--portrait)" role="img" aria-label="Porträt Teammitglied"/>
      <circle cx="484" cy="86" r="50" fill="var(--portrait)" role="img" aria-label="Porträt Teammitglied"/>
      <circle cx="85" cy="719" r="50" fill="var(--portrait)" role="img" aria-label="Porträt Teammitglied"/>
      <circle cx="199" cy="719" r="50" fill="var(--portrait)" role="img" aria-label="Porträt Teammitglied"/>
      <circle cx="316" cy="719" r="50" fill="var(--portrait)" role="img" aria-label="Porträt Teammitglied"/>
    </g>
  </svg>

  <div class="hub-name">WERKSINN</div>

  <article class="block block--credo">
    <h2>CREDO</h2>
    <h3>Woran wir glauben</h3>
    <p>Wir glauben, dass sich persönliche und ökonomische Werte ergänzen - mehr noch, dass sie langfristig nicht ohne einander auskommen und dass sich emotionale Bindung als Mehrwert in Zahlen ausdrückt.</p>
  </article>

  <article class="block block--value">
    <h2>MEHRWERT</h2>
    <h3>Was wir bieten</h3>
    <p>Kundare heißt marktschreierisch anpreisen, hinters Licht führen, täuschen, Mandare heißt beauftragen, Vertrauen schenken.</p>
    <p>Wir legen großen Wert auf eine Beziehung, die Mandare, nicht Kundare entspricht.</p>
    <p>Für uns ist der partnerschaftliche Umgang mit unseren Mandanten das Fundament.</p>
    <p><strong>Wir haben keine Kunden.<br>Wir unterstützen Mandanten.</strong></p>
  </article>

  <article class="block block--mission">
    <h2>MISSION</h2>
    <h3>Was unser handeln leitet</h3>
    <p>Wir beraten Unternehmen im Rahmen der Talentförderung und helfen Jugendlichen auf den Weg ins Berufsleben.</p>
    <p>Für Unternehmen</p>
    <ul style="margin-top:10px">
      <li>Talentförderung &amp; Talent Managment</li>
      <li>Professionalisierung der Personalarbeit</li>
      <li>Organisationsentwicklung</li>
      <li>Potentialorientierte Mitarbeiterführung</li>
    </ul>
    <p>Für die Junge Generation</p>
    <ul>
      <li>&nbsp;Berufsorientierung</li>
      <li>Bewerbungscoaching</li>
    </ul>
  </article>
</section>

</body>
</html>
```